Rehabilitation Centre Driving Evaluation brochure

I have already designed a brochure when I was at my previous workplace, but need a new one for my own rehab clinic. I will attach the brochure that I already did, as the information hasn't really changed. It is just very old and very ugly. It is an information pamphlet that will be in physician offices. Please let me know if you need anything else.

Target Market(s)

physicians, rehabilitation professionals, therapists, and individuals with medical conditions who want to return to driving

Industry/Entity Type

Medical

Requirements
Nice to have
• I am not stuck on the trifold, and actually may prefer a single fold brochure.

```html
<!DOCTYPE html>
<html lang="en">
<head>
<meta charset="utf-8">
<title>Driving Evaluation and Training Center Brochure</title>
<link rel="stylesheet" href="https://fonts.googleapis.com/css2?family=Oswald:wght@600&family=Questrial&display=swap">
<style>
  :root {
    --navy: #173f5f;
    --lime: #b5c40f;
    --white: #ffffff;
    --ink: #2b2b2b;
    --muted: #b9b9b9;
    --stage: #e8e5e0;
    --photo-dark: #3a3a3a;
    --photo-light: #8a8a8a;
    --dash-warm: #c9a273;
    --dash-dark: #2f3439;
  }
  * { margin: 0; padding: 0; box-sizing: border-box; }
  html, body { width: 989px; height: 1200px; overflow: hidden; }
  body { background: var(--stage); font-family: "Questrial", "Century Gothic", sans-serif; position: relative; }
  .panel { position: absolute; left: 120px; width: 760px; height: 536px; background: var(--white); overflow: hidden; }
  .panel--cover { top: 42px; }
  .panel--inside { top: 622px; }
  .panel-shapes { position: absolute; inset: 0; }
  .abs { position: absolute; }

  .brand { display: flex; align-items: center; gap: 8px; color: var(--navy); }
  .brand-dot { width: 16px; height: 16px; border-radius: 50%; background: var(--lime); flex: none; }
  .brand-name { line-height: 1.15; }
  .brand--cover { left: 586px; top: 104px; width: 150px; font-size: 15px; }
  .brand--contact { left: 272px; top: 426px; width: 110px; font-size: 11px; color: var(--white); gap: 6px; }
  .brand--contact .brand-dot { width: 11px; height: 11px; }

  .section-title { font-size: 15px; color: var(--navy); font-weight: 400; }
  .section-title--light { color: var(--white); }
  .band-copy { color: var(--white); font-size: 9.6px; line-height: 1.18; }
  .band-copy p + p { margin-top: 11px; }

  .contact { left: 32px; top: 370px; color: var(--white); font-size: 10.3px; list-style: none; }
  .contact li { display: flex; align-items: flex-start; gap: 8px; margin-bottom: 6px; }
  .contact svg { width: 10px; height: 10px; flex: none; margin-top: 1px; }

  .cover-title { left: 410px; top: 380px; font-family: "Oswald", "Arial Narrow", sans-serif; font-weight: 600; font-size: 31px; line-height: 1.02; letter-spacing: -0.5px; color: var(--white); }
  .cover-title .accent { color: var(--lime); display: block; }
  .cover-sub { left: 412px; top: 458px; font-size: 15px; color: var(--white); }
  .cover-url { left: 412px; top: 510px; font-size: 10px; color: var(--muted); }

  .body-copy { color: var(--ink); font-size: 9.2px; line-height: 1.18; }
  .body-copy p + p { margin-top: 8px; }
  .service-title { font-size: 11.5px; color: var(--navy); font-weight: 700; margin-bottom: 5px; }
</style>
</head>
<body>

<section class="panel panel--cover">
  <svg class="panel-shapes" viewBox="0 0 760 536" aria-hidden="true">
    <rect x="0" y="336" width="760" height="160" fill="var(--navy)"/>
    <polygon points="0,170 472,170 406,348 0,348" fill="var(--lime)"/>
    <polygon points="504,160 760,160 760,170 500,170" fill="var(--lime)"/>
    <polygon points="448,326 760,326 760,336 444,336" fill="var(--lime)"/>
    <defs>
      <linearGradient id="roadPhoto" x1="0" y1="0" x2="1" y2="1">
        <stop offset="0" stop-color="var(--photo-light)"/>
        <stop offset="1" stop-color="var(--photo-dark)"/>
      </linearGradient>
    </defs>
  </svg>
  <svg class="abs" style="left:0;top:0" width="760" height="536" viewBox="0 0 760 536" role="img" aria-label="Photo of a car on a misty forest road">
    <polygon points="480,170 760,170 760,326 422,326" fill="url(#roadPhoto)"/>
  </svg>

  <div class="abs brand brand--cover"><span class="brand-dot"></span><span class="brand-name">Northway Rehabilitation Associates</span></div>

  <h2 class="abs section-title" style="left:30px;top:140px">Referral Process</h2>
  <div class="abs band-copy" style="left:30px;top:190px;width:316px">
    <p>Referrals maybe made by physicians, therapists, individuals requiring service, insurance companies, case managers, community service agencies, etc. The referral source will be asked to complete a referral form. The client's physician will be contacted and asked to complete a medical referral form stating the client is medically able to participate in the assesment.</p>
    <p>Referrals can be made for any individual who requires an evaluation of their driving skills or adaptive equipment needs by contacting us.</p>
  </div>

  <ul class="abs contact">
    <li><svg viewBox="0 0 10 10"><path d="M5 0.5a3.3 3.3 0 0 1 3.3 3.3C8.3 6.3 5 9.5 5 9.5S1.7 6.3 1.7 3.8A3.3 3.3 0 0 1 5 .5z" fill="none" stroke="var(--lime)"/><circle cx="5" cy="3.8" r="1.1" fill="var(--lime)"/></svg><span>2480 Alder Crescent, Unit #4<br>Riverside, Ontario, K2P 3M5</span></li>
    <li style="margin-top:4px"><svg viewBox="0 0 10 10"><path d="M2 .8l1.8 2-1 1.2a6 6 0 0 0 3.2 3.2l1.2-1 2 1.8-1 1.5C4.6 9.3.7 5.4.5 1.8z" fill="var(--lime)"/></svg><span>555 014 2270</span></li>
    <li><svg viewBox="0 0 10 10"><rect x="2.5" y="0.8" width="5" height="2.5" fill="var(--lime)"/><rect x="0.5" y="3.5" width="9" height="4" rx="1" fill="var(--lime)"/><rect x="2.5" y="6.5" width="5" height="3" fill="var(--lime)"/></svg><span>555 014 2271</span></li>
    <li><svg viewBox="0 0 10 10"><rect x="0.5" y="1.8" width="9" height="6.4" fill="none" stroke="var(--lime)"/><path d="M.5 1.8 5 5.6 9.5 1.8" fill="none" stroke="var(--lime)"/></svg><span>office@northwayrehab.ca</span></li>
    <li><svg viewBox="0 0 10 10"><circle cx="5" cy="5" r="4.4" fill="none" stroke="var(--lime)"/><ellipse cx="5" cy="5" rx="1.9" ry="4.4" fill="none" stroke="var(--lime)"/><path d="M.6 5h8.8M1.5 2.7h7M1.5 7.3h7" stroke="var(--lime)" stroke-width=".7"/></svg><span>www.northwayrehab.ca</span></li>
  </ul>

  <div class="abs brand brand--contact"><span class="brand-dot"></span><span class="brand-name">Northway Rehabilitation</span></div>

  <h1 class="abs cover-title">DRIVING EVALUATION<span class="accent">AND TRAINING CENTER</span></h1>
  <p class="abs cover-sub">A comprehensive driver rehabilitation program</p>
  <p class="abs cover-url">www.northwayrehab.ca</p>
</section>

<section class="panel panel--inside">
  <svg class="panel-shapes" viewBox="0 0 760 536" aria-hidden="true">
    <polygon points="0,0 444,0 428,50 0,50" fill="var(--navy)"/>
    <polygon points="0,50 412,50 352,222 0,222" fill="var(--lime)"/>
    <polygon points="600,0 760,0 760,18 594,18" fill="var(--lime)"/>
    <polygon points="564,107 760,107 760,114 560,114" fill="var(--lime)"/>
    <rect x="0" y="530" width="760" height="6" fill="var(--navy)"/>
    <defs>
      <linearGradient id="wheelPhoto" x1="0" y1="0" x2="1" y2="0">
        <stop offset="0" stop-color="var(--dash-warm)"/>
        <stop offset="1" stop-color="var(--dash-dark)"/>
      </linearGradient>
    </defs>
  </svg>
  <svg class="abs" style="left:0;top:0" width="760" height="536" viewBox="0 0 760 536" role="img" aria-label="Photo of a hand on a car steering wheel">
    <polygon points="444,18 760,18 760,107 408,107" fill="url(#wheelPhoto)"/>
  </svg>
  <svg class="abs" style="left:12px;top:59px" width="68" height="83" viewBox="0 0 68 83" role="img" aria-label="Medical caduceus symbol">
    <rect width="68" height="83" rx="4" fill="#5f6a10"/>
  </svg>

  <h2 class="abs section-title section-title--light" style="left:79px;top:26px">Reason for Assesment</h2>
  <div class="abs band-copy" style="left:87px;top:60px;width:272px">
    <p>Each physician is required by law to report to the Ministry of Transportation any individual whose driving skills maybe affected as a result of illnes or injury. Therefore, the client's driver's licence maybe placed under medical suspension. If this occurs, the client will be asked to undergo a driving evaluation from an Ontario Driver Assesment Centre.</p>
    <p>Individuals affected by illness, injury, or the aging process, whose driving skills have the potential to be affected, are also encouraged to undergo an evaluation of driving skills. The evaluation is designed to assess each client's ability to safely operate a motor vehicle and provide recommendations as needed.</p>
  </div>

  <h2 class="abs section-title" style="left:21px;top:246px">Eligibility</h2>
  <div class="abs body-copy" style="left:21px;top:272px;width:340px">
    <p>Most individuals with disabilities are eligible for an evaluation of their ability to drive. Clients must have a valid driver's licence or the ability to obtain a temporary driver's licence or learner's permit.</p>
  </div>

  <h2 class="abs section-title" style="left:21px;top:338px">What we do?</h2>
  <div class="abs body-copy" style="left:21px;top:370px;width:342px">
    <p>Northway rehabilitation associates commited to providing optimal rehabilitation service in a cost effective manner.</p>
    <p>We Offer a multi-disciplinary, client-centred program of assesment, treatment and consultation for clients with physical, cognitive and/or perceptual impairments. We are aware each client is unique, therefore each program is tailored according to the individual's needs and personal goals.</p>
    <p>The driving assessment and training program is part of our comprehensive rehabilitation services. It is a service which represents our dedication to assist all individuals achieve optimal independence. Driving is an integral skill which is often essential for independence in the community</p>
  </div>

  <h2 class="abs section-title" style="left:404px;top:126px">Program Components &amp; Services</h2>

  <div class="abs" style="left:405px;top:160px;width:328px">
    <h3 class="service-title">Clinical Evaluation</h3>
    <div class="body-copy"><p>The client is assessed by a certified occupational therapist/ Th client is initially seen in clinic for an assessment of physical, cognitive, and perceptual functioning as they relate to driving. The in-clinic portion of the assessment provided the therapist with information regarding medical history, driving history, knowledge of road signs and driving rules, physical abilities, cognitive status, visual and perceptual skills.</p></div>
  </div>

  <div class="abs" style="left:405px;top:269px;width:328px">
    <h3 class="service-title">On the Road Evaluation</h3>
    <div class="body-copy"><p>Following the in-clinic assessment, each client is the assessed in car by the therapist together with a certified driving instructor. The portion of the evaluation provides valuable information regarding the individual's functional driving skills.</p></div>
  </div>

  <div class="abs" style="left:405px;top:354px;width:328px">
    <h3 class="service-title">Evaluation Equipment Needs</h3>
    <div class="body-copy"><p>During the evaluation, it will be determined whether adaptive equipment will be necessary to improve the client's ability to drive safely. Recommendations will be made for adaptive equipment and installation</p></div>
  </div>

  <div class="abs" style="left:405px;top:428px;width:328px">
    <h3 class="service-title">Training &amp;Follow-up Services</h3>
    <div class="body-copy"><p>Clients are commonly seen following a driving evaluation for training with driving skills or adaptive equipment. Furthur involvement with the occupational therepist maybe indicated for cognitive or perceptual retraining, mobility-aid prescription, vehicle modification, or consultation with appropriate new vehicle purchase</p></div>
  </div>
</section>

</body>
</html>
```